Ward Compass Business Card Design*

We need a business card design for our company Ward Compass. Our company is specialized in providing online consulting services regarding medical institutions, hospitals and doctors. We work with patients worldwide looking to choose between healthcare providers. We have a website you may use as a reference, where we list doctors and clinics worldwide. So we target Medical providers as well as patients worldwide.
Target Market(s)
Medical Providers and patients around the world
Industry/Entity Type
Medical
Contact Information for Business Card
Salwa Kettani
CEO
+90 612 348 2175
info@wardcompass.example
www.wardcompass.example
14 Annakhil 7 H.R.B. Rabat, Morocco
Requirements
Must have
- Company logo/name on one full side, personal info and smaller logo and company name on the other side.
Nice to have
- Smart and elegant design

```html
<!DOCTYPE html>
<html lang="en">
<head>
<meta charset="utf-8">
<title>Ward Compass — Business Card</title>
<link rel="stylesheet" href="https://fonts.googleapis.com/css2?family=Nunito+Sans:wght@300;400;700;800&display=swap">
<style>
  :root {
    --backdrop: #e6e2dc;
    --card-light: #f3f3f5;
    --brand-blue: #1a4373;
    --text-grey: #58585b;
    --rule-grey: #9a9a9d;
    --rule-blue: #2b3fa8;
    --mark-grey: #8a8a8c;
    --white: #ffffff;
  }
  * { margin: 0; padding: 0; box-sizing: border-box; }
  html, body {
    width: 900px; height: 1200px; overflow: hidden;
    background: var(--backdrop);
    font-family: "Nunito Sans", "Helvetica Neue", Arial, sans-serif;
  }
  .canvas { position: relative; width: 900px; height: 1200px; }

  .card {
    position: absolute; left: 78px; width: 745px; height: 436px;
    box-shadow: 0 3px 6px rgba(0,0,0,0.25);
  }
  .card-front { top: 134px; background: var(--card-light); }
  .card-back { top: 638px; background: var(--brand-blue); }

  .brand { position: absolute; display: flex; align-items: center; }
  .brand-dot { border-radius: 50%; flex: none; }
  .brand-name { font-weight: 800; text-transform: uppercase; white-space: nowrap; }

  .card-front .brand { left: 47px; top: 71px; gap: 14px; }
  .card-front .brand-dot { width: 64px; height: 64px; background: var(--brand-blue); }
  .card-front .brand-name { font-size: 29px; color: var(--brand-blue); letter-spacing: 0.2px; }

  .person { position: absolute; left: 50px; top: 240px; }
  .person-name { font-size: 26px; line-height: 32px; color: var(--text-grey); font-weight: 400; text-transform: uppercase; }
  .person-name .given { font-weight: 800; color: var(--brand-blue); }
  .person-role { font-size: 17px; line-height: 22px; color: var(--text-grey); font-weight: 300; margin-top: 2px; }

  .rule { position: absolute; top: 294px; height: 1px; }
  .rule-accent { left: 100px; width: 164px; background: var(--rule-blue); }
  .rule-base { left: 266px; width: 435px; background: var(--rule-grey); }

  .contacts { position: absolute; left: 51px; top: 346px; list-style: none; }
  .contacts li { display: flex; align-items: center; height: 26px; font-size: 17.5px; color: var(--text-grey); font-weight: 300; }
  .contacts svg { width: 20px; height: 20px; margin-right: 17px; flex: none; }

  .address { position: absolute; right: 42px; top: 350px; font-size: 17.5px; line-height: 23px; color: var(--text-grey); font-weight: 400; font-style: normal; }

  .card-back .brand { left: 125px; top: 156px; gap: 22px; }
  .card-back .brand-dot { width: 120px; height: 120px; background: var(--white); }
  .card-back .brand-name { font-size: 46px; color: var(--white); }

  .website {
    position: absolute; left: 0; right: 0; top: 388px; text-align: center;
    font-size: 17px; letter-spacing: 4px; color: var(--white); font-weight: 400;
  }
</style>
</head>
<body>
<main class="canvas">
  <section class="card card-front" aria-label="Card front">
    <div class="brand">
      <span class="brand-dot"></span>
      <span class="brand-name">Ward Compass</span>
    </div>

    <div class="person">
      <p class="person-name"><span class="given">Salwa</span> Kettani</p>
      <p class="person-role">CEO</p>
    </div>
    <span class="rule rule-accent"></span>
    <span class="rule rule-base"></span>

    <ul class="contacts">
      <li>
        <svg viewBox="0 0 20 20" aria-hidden="true">
          <circle cx="10" cy="10" r="10" fill="#1a4373"/>
          <path d="M7.2 5.2l1.6 2.1-1 1.2c.6 1.3 1.6 2.3 2.8 2.9l1.2-1 2.1 1.6-.9 1.9c-3.8-.3-6.7-3.2-7-7z" fill="#ffffff"/>
        </svg>
        +90 612 348 2175
      </li>
      <li>
        <svg viewBox="0 0 20 20" aria-hidden="true">
          <circle cx="10" cy="10" r="10" fill="#1a4373"/>
          <rect x="5.5" y="6.8" width="9" height="6.4" rx="0.8" fill="#ffffff"/>
          <path d="M5.8 7.2l4.2 3.2 4.2-3.2" fill="none" stroke="#1a4373" stroke-width="1"/>
        </svg>
        info@wardcompass.example
      </li>
    </ul>

    <address class="address">14 Annakhil 7 H.R.B.<br>Rabat, Morocco</address>
  </section>

  <section class="card card-back" aria-label="Card back">
    <div class="brand">
      <span class="brand-dot"></span>
      <span class="brand-name">Ward Compass</span>
    </div>
    <p class="website">www.wardcompass.example</p>
  </section>
</main>
</body>
</html>
```